Video Streaming Website Design Needed

We are a non-profit organization and currently have a website called LumenHourly.com
We want to launch a new version of the site that will look completely different. It is a video streaming site. We have the programmers who will work on it but we just need a designer.
We have an idea of what we want the layout to be. You can check out samples of the idea we have for the rough layout.
http://lumenhourly.com/images/LH_2.0_Homepage2.jpg
http://lumenhourly.com/images/LH_2.0_Video_Page.jpg
http://lumenhourly.com/images/LH_2.0_Individual_Speakers_Page.jpg
http://lumenhourly.com/images/LH_2.0_Registration_Page.jpg
Those are just some of our pages we plan on having.
This is a Jewish site and we have holidays through out the year and we would like to incorporate sort of a theme for each holiday using a background design change. For example, this site http://images.pvd7.layoutbarn-demo.com/qx_48217/index.html , has a nice background and maybe we can use a similar idea to change the theme of the background depending on the holiday.
Target Market(s)
Jews and spiritual minded people. Men & Women. Ages 16-55.
Industry/Entity Type
Non-Profit
Look and feel
Each slider illustrates characteristics of the customer's brand and the style your logo design should communicate.

```html
<!DOCTYPE html>
<html lang="en">
<head>
<meta charset="utf-8">
<title>LumenHourly.com – Home</title>
<link rel="stylesheet" href="https://fonts.googleapis.com/css2?family=Arimo:wght@400;700&display=swap">
<style>
:root{
  --bg-deep:#1c4fa8;
  --bg-light:#8fbfe6;
  --brand:#0b4fc4;
  --brand-dark:#0a3f9e;
  --nav-top:#3aa0ef;
  --nav-bottom:#0d5cd1;
  --panel-edge:#d2d2d2;
  --ink:#333;
  --ink-soft:#555;
  --muted:#8a8a8a;
  --link:#2fa6e8;
  --row-alt:#d9deea;
  --white:#fff;
}
*{box-sizing:border-box;margin:0;padding:0}
html,body{width:1200px;height:952px;overflow:hidden}
body{font-family:"Arimo",Arial,sans-serif;color:var(--ink);position:relative;background:var(--bg-deep)}
.backdrop{position:absolute;inset:0;
  background:radial-gradient(ellipse at 85% 60%,#c9e2f5 0%,#6aa6dc 30%,transparent 55%),
  radial-gradient(ellipse at 10% 80%,#7eb3e2 0%,transparent 45%),
  linear-gradient(180deg,#1e4ea6 0%,#3b7cc9 50%,var(--bg-light) 100%)}
.page{position:absolute;left:204px;top:59px;width:794px;height:828px;background:var(--white);border-radius:8px;box-shadow:0 2px 10px rgba(0,0,0,.25)}
.abs{position:absolute}
.logo{left:14px;top:22px;display:flex;align-items:center;gap:8px}
.logo-dot{width:34px;height:34px;border-radius:50%;background:var(--brand)}
.logo-name{font-size:27px;font-weight:700;color:var(--brand);letter-spacing:-.5px}
.dateline{right:118px;top:7px;font-size:10px;color:var(--ink-soft);text-align:right;line-height:15px}
.dateline a{color:var(--brand);text-decoration:none}
.dateline span{color:var(--muted)}
.donate{right:10px;top:0;width:103px;height:37px;border-radius:0 0 5px 5px;
  background:linear-gradient(#2a86e8,#0c4fc2);color:#fff;font-size:15px;font-weight:700;
  display:flex;align-items:center;justify-content:center;letter-spacing:-.3px}
.donate em{font-style:normal;color:#8fd0ff}
.nav{left:10px;top:92px;width:776px;height:41px;border-radius:4px;background:linear-gradient(var(--nav-top),var(--nav-bottom))}
.nav a{position:absolute;top:14px;font-size:11px;font-weight:700;color:#fff;text-decoration:none}
.search{left:520px;top:8px;width:249px;height:25px;background:#fff;border-radius:3px;border:1px solid #9cc6ee}
.search svg{position:absolute;left:6px;top:4px}
.search .ph{position:absolute;left:34px;top:7px;font-size:10px;color:#444}
.search .bar{position:absolute;left:27px;top:3px;width:1px;height:17px;background:#ccc}
.search .go{position:absolute;right:1px;top:1px;width:57px;height:21px;border-radius:2px;
  background:linear-gradient(#2e8ff0,#0c57cc);color:#fff;font-size:11px;font-weight:700;display:flex;align-items:center;justify-content:center}
.hero{left:10px;top:140px;width:512px;height:306px;border-radius:5px;overflow:hidden;background:#e9e9e9}
.hero-photo{position:absolute;left:0;top:0;width:512px;height:231px;
  background:radial-gradient(ellipse at 55% 55%,#d9a58a 0%,#b3735a 35%,#7a3a2a 70%,#4a1f18 100%)}
.hero-tag{position:absolute;left:14px;top:8px;font-size:12px;font-weight:700;color:#fff;letter-spacing:.2px}
.hero-caption{position:absolute;left:14px;top:236px;font-size:10.6px;line-height:13.3px;color:var(--brand-dark)}
.hero-caption h2{font-size:15px;color:var(--brand);margin-bottom:2px}
.stats{left:10px;top:454px;width:512px;height:170px;border-radius:5px;background:linear-gradient(#dedede,#efefef);border:1px solid var(--panel-edge)}
.stats h3{position:absolute;left:17px;top:10px;font-size:17px;font-weight:400;color:var(--link);letter-spacing:-.4px}
.stat{position:absolute;font-size:12px;color:var(--link);white-space:nowrap}
.stat b{position:absolute;left:-48px;top:-2px;width:40px;font-size:15px;font-weight:400;color:#555;text-align:right}
.side{left:530px;top:140px;width:256px;height:485px;background:#efefef;border-radius:4px;overflow:hidden}
.tabs{position:absolute;left:0;top:0;width:256px;height:34px;background:linear-gradient(#3aa0ef,#0d5cd1);display:flex}
.tabs span{height:34px;display:flex;align-items:center;justify-content:center;font-size:10px;font-weight:700;color:#fff;border-right:1px solid #7cc0f5}
.tabs .on{background:#e9e9e9;color:#222;border-radius:3px 3px 0 0}
.list{position:absolute;left:10px;top:44px;width:231px}
.item{position:relative;height:55px;font-size:9.4px;line-height:13.8px;color:#444}
.item.alt{background:var(--row-alt)}
.thumb{position:absolute;left:0;top:0;width:49px;height:49px;background:linear-gradient(135deg,#6b6b6b,#2b2b2b 60%,#1a1a1a)}
.item .txt{position:absolute;left:57px;top:4px;white-space:nowrap}
.item .txt b{color:#333}
.scroll{position:absolute;right:3px;top:44px;width:10px;height:440px;background:#f8f8f8;border-left:1px solid #ddd}
.scroll i{position:absolute;left:1px;top:34px;width:7px;height:58px;border-radius:4px;background:#ddd;border:1px solid #bbb}
.partners{left:10px;top:633px;width:776px;height:107px;border-radius:5px;background:#e8e8e8}
.partners p{position:absolute;left:16px;top:12px;font-size:10.5px;color:var(--muted)}
.partner{position:absolute;top:50px;font-size:22px;font-weight:700;color:#9a9a9a;letter-spacing:-.5px}
.footer{left:0;top:750px;width:794px;text-align:center;font-size:9.3px;line-height:14px;color:var(--muted)}
.footer strong{display:block;color:var(--brand-dark);font-size:10px;margin-bottom:2px}
</style>
</head>
<body>
<div class="backdrop" role="img" aria-label="Full-page blue-toned photograph of a man in a prayer shawl blowing a shofar"></div>
<main class="page">
  <div class="abs logo"><span class="logo-dot"></span><span class="logo-name">LumenHourly</span></div>
  <div class="abs dateline">Wednesday May 18 2011 - Lyar 14, 5771<br><a href="#">Join Now</a> <span>|</span> <span style="color:#666">Login</span></div>
  <div class="abs donate">Donate<em>Now</em></div>

  <nav class="abs nav">
    <a style="left:19px" href="#">About Torah</a>
    <a style="left:105px" href="#">Videos</a>
    <a style="left:160px" href="#">Speakers</a>
    <a style="left:229px" href="#">Jewish Links</a>
    <a style="left:316px" href="#">Contact Us</a>
    <a style="left:395px" href="#">Privacy &amp; Terms</a>
    <div class="abs search">
      <svg width="17" height="17" viewBox="0 0 17 17"><circle cx="7" cy="7" r="5" fill="none" stroke="#aaa" stroke-width="1.5"/><line x1="11" y1="11" x2="15" y2="15" stroke="#aaa" stroke-width="2"/></svg>
      <span class="bar"></span><span class="ph">Search</span>
      <span class="go">Search</span>
    </div>
  </nav>

  <section class="abs hero">
    <div class="hero-photo" role="img" aria-label="Close-up photograph of the featured lecturer"></div>
    <div class="hero-tag">UPCOMING LECTURES &amp; EVENTS</div>
    <div class="hero-caption">
      <h2>Saturday Night</h2>
      LumenHourly Video Presentation - Saturday Nights at 8:30pm<br>
      Free pizza will be served!<br>
      Location : Beth Orah Congregation - 41-20 Linden Avenue, Maple Park 10482
    </div>
  </section>

  <section class="abs stats">
    <h3>Site Statistics</h3>
    <svg class="abs" style="left:26px;top:52px" width="96" height="98" viewBox="0 0 96 98">
      <polygon points="4,84 70,64 92,74 26,96" fill="#cfcfcf"/>
      <rect x="12" y="48" width="9" height="38" fill="#333"/>
      <rect x="24" y="36" width="9" height="46" fill="#2f8ee6"/>
      <rect x="36" y="42" width="9" height="37" fill="#666"/>
      <rect x="48" y="22" width="9" height="54" fill="#1f6fd4"/>
      <rect x="60" y="4" width="9" height="68" fill="#222"/>
      <rect x="72" y="30" width="9" height="38" fill="#888"/>
    </svg>
    <div class="stat" style="left:185px;top:61px"><b>1</b>Videos Added Today</div>
    <div class="stat" style="left:185px;top:84px"><b>12</b>Videos Added This Week</div>
    <div class="stat" style="left:185px;top:107px"><b>15</b>Videos Added This Month</div>
    <div class="stat" style="left:185px;top:130px"><b>42</b>Added This Year</div>
    <div class="stat" style="left:408px;top:61px"><b>203</b>Members</div>
    <div class="stat" style="left:408px;top:84px"><b>12</b>Online</div>
    <div class="stat" style="left:408px;top:107px"><b>4</b>Events</div>
    <div class="stat" style="left:408px;top:130px"><b>152</b>Catagories</div>
  </section>

  <aside class="abs side">
    <div class="tabs">
      <span class="on" style="width:56px">Latest</span>
      <span style="width:87px">Bookmarks</span>
      <span style="width:51px">Tags</span>
      <span style="width:62px;border:none">Random</span>
    </div>
    <div class="list">
      <div class="item alt"><div class="thumb" role="img" aria-label="Lecturer thumbnail"></div><div class="txt"><b>Meir Kalderon</b><br>Yonatan<br>10.09.2011</div></div>
      <div class="item"><div class="thumb" role="img" aria-label="Lecturer thumbnail"></div><div class="txt"><b>Don’t work in the auto industry</b><br>R. Eli Sandberg<br>10.09.2011</div></div>
      <div class="item alt"><div class="thumb" role="img" aria-label="Lecturer thumbnail"></div><div class="txt"><b>Your Mistaking me for the singer</b><br>R. Avi Tolan<br>10.09.2011</div></div>
      <div class="item"><div class="thumb" role="img" aria-label="Lecturer thumbnail"></div><div class="txt"><b>Your All Going to Hell!</b><br>R. Yonatan<br>10.09.2011</div></div>
      <div class="item alt"><div class="thumb" role="img" aria-label="Lecturer thumbnail"></div><div class="txt"><b>That will be 50% Off</b><br>R. Yonatan<br>10.09.2011</div></div>
      <div class="item"><div class="thumb" role="img" aria-label="Lecturer thumbnail"></div><div class="txt"><b>Screen Time is Evil</b><br>R. Yonatan<br>10.09.2011</div></div>
      <div class="item alt"><div class="thumb" role="img" aria-label="Lecturer thumbnail"></div><div class="txt"><b>I Don’t work in the auto industry</b><br>R. Yonatan<br>10.09.2011</div></div>
      <div class="item"><div class="thumb" role="img" aria-label="Lecturer thumbnail"></div><div class="txt"><b>Don’t work in the auto industry</b><br>R. Eli Sandberg<br>10.09.2011</div></div>
    </div>
    <div class="scroll"><i></i></div>
  </aside>

  <section class="abs partners">
    <p>All of the learning today on LumenHourly.com is dedicated to:</p>
    <span class="partner" style="left:24px">kesher.org</span>
    <span class="partner" style="left:196px">ARVO</span>
    <span class="partner" style="left:330px">Naviah</span>
    <span class="partner" style="left:432px">Daily Law Notes</span>
    <span class="partner" style="left:628px">TheThinker</span>
  </section>

  <footer class="abs footer">
    <strong>© Copyright LumenHourly.com 2007 - 2011. All Rights Reserved.</strong>
    The content on Lumenhourly.com and related sites is for personal use only. It may not be distributed,<br>
    duplicated, broadcasted or otherwise reproduced in any way, shape or form without express written<br>
    permission from us. For permission to show content publicly, please contact us at hello@lumenhourly.org
  </footer>
</main>
</body>
</html>
```